Awesome design needed for standup comedy portal

We need a website designed for a new portal (grinbox.net) dedicated to standup comedy.

- homepage
- featured "hero" content at top
- banner advertising
- browse comics
- browse venues
- search
- signup / login
- social media links

- comic page
- name
- pictures
- calendar of performances
- list of albums (with buy buttons)
- list of specials (Vexora, Plumtrack, etc. with buy buttons)
- reviews
- latest tweets
- latests pixaloop photos
- links to social media accounts
- links to filmdex, podcast

- venue page
- name
- pictures
- address, phone number
- calendar of events
- reviews
- latest tweets
- links to filmdex, podcast

Target Market(s)

Fans of standup comedy and comedians

Number of Pages Required

Font styles to use
Sans Serif

Requirements
Must have
• Will eventually be implemented in bootstrap, so please keep that in mind

```html
<!DOCTYPE html>
<html lang="en">
<head>
<meta charset="utf-8">
<title>Grinbox – Standup Comedy Portal</title>
<link rel="stylesheet" href="https://fonts.googleapis.com/css2?family=Oswald:wght@400;500&family=Open+Sans:wght@400;600&display=swap">
<style>
:root{
  --red:#c0111b;
  --red-dark:#8f1116;
  --ink:#333;
  --muted:#666;
  --line:#d0d0d0;
  --dark:#1e1e1e;
  --white:#fff;
}
*{box-sizing:border-box;margin:0;padding:0}
html,body{width:1200px;height:2517px;overflow:hidden}
body{font-family:"Open Sans",Arial,sans-serif;color:var(--ink);background:var(--white);position:relative}
.head,.title{font-family:"Oswald","Arial Narrow",sans-serif;font-weight:400}
section,header,footer{position:absolute;left:0;width:1200px}

/* header */
.site-header{top:0;height:92px;background:var(--white)}
.main-nav{position:absolute;left:133px;top:32px;display:flex;gap:20px;font-family:"Oswald",sans-serif;font-size:16px;color:#222}
.main-nav a{color:inherit;text-decoration:none;padding-bottom:4px}
.main-nav a.active{color:var(--red);border-bottom:2px solid var(--red)}
.brand{position:absolute;left:528px;top:8px;width:144px;height:128px;background:var(--red);border-radius:50%/45%;border:5px solid var(--white);display:flex;align-items:center;justify-content:center;z-index:3}
.brand span{font-family:"Oswald",sans-serif;font-weight:500;font-size:30px;color:var(--white)}
.search{position:absolute;left:747px;top:30px;width:168px;border-bottom:1px solid #999;padding-bottom:6px;font-family:"Oswald",sans-serif;font-size:15px;color:#999}
.search svg{position:absolute;right:2px;top:3px}
.auth{position:absolute;top:28px;display:flex;gap:9px;left:931px}
.auth a{border:1px solid #999;border-radius:3px;padding:4px 9px;font-family:"Oswald",sans-serif;font-size:15px;color:#555;text-decoration:none}

/* hero */
.hero{top:92px;height:521px;background:linear-gradient(90deg,#6f6d6a,#8a807a 35%,#746a66 60%,#5b5957)}
.hero::after{content:"";position:absolute;inset:0;background:rgba(20,20,20,.25)}
.hero-photo{position:absolute;inset:0}
.hero-text{position:absolute;left:0;right:0;top:296px;text-align:center;color:var(--white);z-index:2}
.hero-text h1{font-size:34px;font-family:"Oswald",sans-serif;font-weight:400}
.hero-text p{font-size:11px;line-height:16px;width:640px;margin:4px auto 0}
.btn-light{display:inline-flex;align-items:center;gap:8px;background:var(--white);color:#222;font-family:"Oswald",sans-serif;font-size:16px;padding:0 18px;height:50px;margin-top:24px;border-radius:3px}
.hero-arrow{position:absolute;top:245px;width:36px;height:36px;border-radius:50%;background:rgba(255,255,255,.35);z-index:2;display:flex;align-items:center;justify-content:center}

/* welcome */
.welcome{top:613px;height:503px}
.welcome-photo{position:absolute;left:114px;top:50px;width:202px;height:372px;background:linear-gradient(180deg,#f3f3f3,#dcdcdc)}
.welcome-body{position:absolute;left:362px;top:105px;width:705px}
.section-title{font-family:"Oswald",sans-serif;font-weight:400;color:var(--red);font-size:33px;line-height:44px}
.copy{font-size:11.5px;line-height:22.5px;color:#555;margin-top:14px}
.btn-outline{display:inline-block;margin-top:34px;border:1px solid var(--line);border-radius:3px;width:98px;height:40px;line-height:38px;text-align:center;font-size:11.5px;color:#888}

/* ad banner */
.ad-banner{top:1116px;left:133px;width:934px;height:95px;background:linear-gradient(90deg,#2b2b2b,#4a4a4a 40%,#1c1c1c 70%,#3a3a3a)}
.ad-banner .title{position:absolute;left:229px;top:20px;color:var(--white);font-size:24px}
.ad-banner p{position:absolute;left:229px;top:53px;font-size:11px;color:#bbb}
.btn-red{display:inline-flex;align-items:center;gap:8px;background:var(--red);color:var(--white);font-family:"Oswald",sans-serif;font-size:15px;border-radius:3px}
.ad-banner .btn-red{position:absolute;left:547px;top:27px;height:40px;padding:0 16px}

/* comics */
.comics{top:1211px;height:425px}
.comics-body{position:absolute;left:133px;top:70px;width:705px}
.comics-body .copy{margin-top:10px}
.comics-body .btn-red{margin-top:28px;height:52px;padding:0 17px}
.comics-art{position:absolute;left:867px;top:79px;width:200px;height:267px;background:linear-gradient(135deg,#3e7fc1,#c0392b 45%,#2ecc71 80%,#6a8fb3)}

/* programs */
.programs{top:1636px;height:440px;background:radial-gradient(ellipse at 50% 20%,#3a3a3a,#151515 75%)}
.programs-head{position:absolute;top:84px;left:0;right:0;display:flex;justify-content:center;align-items:center;gap:30px;color:var(--white)}
.programs-head .title{font-size:33px}
.nav-box{width:22px;height:22px;border:1px solid #aaa;display:flex;align-items:center;justify-content:center}
.program-list{position:absolute;left:133px;top:151px;display:flex;gap:22px}
.program{width:218px}
.program-thumb{height:160px;position:relative;display:flex;align-items:center;justify-content:center}
.play{width:44px;height:44px;border-radius:50%;background:var(--white);display:flex;align-items:center;justify-content:center}
.program p{font-size:11.5px;line-height:19px;color:#bbb;text-align:center;margin-top:10px}

/* contact */
.contact{top:2076px;height:337px;background:linear-gradient(90deg,var(--red),#b3121a 50%,var(--red-dark))}
.contact .title{position:absolute;top:46px;left:0;right:0;text-align:center;color:var(--white);font-size:33px}
.field{position:absolute;height:39px;border:1.5px solid #f0b0b0;color:#f6d7d7;font-size:11.5px;line-height:36px;padding-left:15px}
.btn-submit{position:absolute;left:560px;top:233px;width:80px;height:39px;background:#1f1f1f;color:var(--white);font-family:"Oswald",sans-serif;font-size:14px;display:flex;align-items:center;justify-content:center;letter-spacing:.5px}

/* footer */
.site-footer{top:2413px;height:104px;background:linear-gradient(90deg,#b0121a,#8c1117);border-top:1px solid #d24a50}
.footer-nav{position:absolute;left:133px;top:31px;font-size:11px;color:#f0c8c8}
.footer-nav span{margin:0 7px}
.copyright{position:absolute;left:133px;top:57px;font-size:10.5px;color:#f0c8c8}
.social{position:absolute;left:956px;top:39px;display:flex;gap:12px}
.social span{width:30px;height:30px;border:1px solid #e49a9e;border-radius:50%}
</style>
</head>
<body>

<header class="site-header">
  <nav class="main-nav">
    <a class="active" href="#">Home</a><a href="#">About</a><a href="#">Venues</a><a href="#">Comics</a><a href="#">Performers</a><a href="#">Contact</a>
  </nav>
  <div class="brand"><span>Grinbox</span></div>
  <div class="search">Search
    <svg width="14" height="14" viewBox="0 0 14 14"><circle cx="6" cy="6" r="4.5" fill="none" stroke="#888" stroke-width="1.6"/><line x1="9.3" y1="9.3" x2="13" y2="13" stroke="#888" stroke-width="1.8"/></svg>
  </div>
  <div class="auth"><a href="#">Log in</a><a href="#">Sign up</a></div>
</header>

<section class="hero">
  <div class="hero-photo" role="img" aria-label="Comedy audience laughing together"></div>
  <span class="hero-arrow" style="left:24px"><svg width="10" height="12"><path d="M8 1 3 6l5 5" fill="none" stroke="#fff" stroke-width="2"/></svg></span>
  <span class="hero-arrow" style="right:24px"><svg width="10" height="12"><path d="M2 1l5 5-5 5" fill="none" stroke="#fff" stroke-width="2"/></svg></span>
  <div class="hero-text">
    <h1>Maecenas interdum tortor risus amet</h1>
    <p>Fusce sem magna, blandit et sem sed, malesuada porta est. Nunc in interdum neque. Proin laoreet, nulla eget fermentum varius, eros felis varius quam at tempus justo est vel nunc. Integer euismod faucibus ipsum, nec lacinia.</p>
    <span class="btn-light"><svg width="10" height="14" viewBox="0 0 10 14"><path d="M5 0a5 5 0 0 0-5 5c0 4 5 9 5 9s5-5 5-9a5 5 0 0 0-5-5z" fill="#222"/><circle cx="5" cy="5" r="1.8" fill="#fff"/></svg>BROWSE VENUES</span>
  </div>
</section>

<section class="welcome">
  <div class="welcome-photo" role="img" aria-label="Comedian on stage with a vintage microphone"></div>
  <div class="welcome-body">
    <h2 class="section-title">Welcome to Grinbox</h2>
    <p class="copy">Suspendisse sed mauris volutpat nisi consectetur vulputate eget vel nisi. Nulla vitae lacus porttitor, iaculis est eget, mattis nulla. Aenean bibendum orci eu eros luctus placerat. In ut enim ut est varius viverra vel a quam. Phasellus varius nisl et diam eleifend, et interdum leo consectetur. Maecenas aliquam purus enim, vel elementum urna convallis nec. Aenean tempor, enim mattis faucibus dignissim, purus tortor consequat felis, ut rutrum lorem turpis ut lorem. Maecenas porta orci a urna pellentesque convallis. Curabitur rutrum lorem in porttitor vulputate. Praesent tortor dui, viverra vel sagittis et, tincidunt ut nisl. Nulla lacinia ligula et porta blandit. Aliquam fringilla lectus nec ligula vestibulum malesuada.</p>
    <span class="btn-outline">Read more</span>
  </div>
</section>

<section class="ad-banner" role="img" aria-label="Banner advert with a theatre crowd and stage performers">
  <div class="title">Fusce fermentum</div>
  <p>Praesent tortor dui, viverra vel sagittis et, tincidunt ut nisl</p>
  <span class="btn-red"><svg width="14" height="12" viewBox="0 0 14 12"><path d="M1 3h12v2a1.5 1.5 0 0 0 0 3v2H1V8a1.5 1.5 0 0 0 0-3z" fill="#fff"/></svg>Book Tickets Now</span>
</section>

<section class="comics">
  <div class="comics-body">
    <h2 class="section-title">Comics</h2>
    <p class="copy">Suspendisse sed mauris volutpat nisi consectetur vulputate eget vel nisi. Nulla vitae lacus porttitor, iaculis est eget, mattis nulla. Aenean bibendum orci eu eros luctus placerat. In ut enim ut est varius viverra vel a quam. Phasellus varius nisl et diam eleifend, et interdum leo consectetur. Maecenas aliquam purus enim, vel elementum urna convallis nec. Aenean tempor, enim mattis faucibus dignissim, purus tortor consequat felis, ut rutrum lorem turpis ut lorem. Maecenas porta orci a urna pellentesque convallis. Curabitur rutrum lorem in porttitor vulputate. Praesent tortor dui, viverra vel sagittis et, tincidunt ut nisl. Nulla lacinia ligula et porta blandit. Aliquam fringilla lectus nec ligula vestibulum malesuada.</p>
    <span class="btn-red"><svg width="12" height="13" viewBox="0 0 12 13"><path d="M2 0h9v10H3a1 1 0 0 0 0 2h8v1H3a2 2 0 0 1-2-2V1z" fill="#fff"/></svg>BROWSE COMICS</span>
  </div>
  <div class="comics-art" role="img" aria-label="Colourful comic book wall art"></div>
</section>

<section class="programs">
  <div class="programs-head">
    <span class="nav-box"><svg width="8" height="10"><path d="M6 1 2 5l4 4" fill="none" stroke="#ddd" stroke-width="1.5"/></svg></span>
    <h2 class="title">Our Programs</h2>
    <span class="nav-box"><svg width="8" height="10"><path d="M2 1l4 4-4 4" fill="none" stroke="#ddd" stroke-width="1.5"/></svg></span>
  </div>
  <div class="program-list">
    <div class="program"><div class="program-thumb" role="img" aria-label="Comedian performing under pink stage lights" style="background:linear-gradient(135deg,#3a4a7a,#8a5a8a 55%,#c2467f)"><span class="play"><svg width="14" height="16"><path d="M2 1l11 7-11 7z" fill="#222"/></svg></span></div><p>Phasellus varius nisl et diam eleifend, et interdum</p></div>
    <div class="program"><div class="program-thumb" role="img" aria-label="Performer in front of a red curtain" style="background:linear-gradient(90deg,#5a0a0a,#a3141a 50%,#4a0808)"><span class="play"><svg width="14" height="16"><path d="M2 1l11 7-11 7z" fill="#222"/></svg></span></div><p>Phasellus varius nisl et diam eleifend, et interdum</p></div>
    <div class="program"><div class="program-thumb" role="img" aria-label="Singer with a retro microphone in low light" style="background:linear-gradient(135deg,#0c0c0c,#3c3c3c 55%,#151515)"><span class="play"><svg width="14" height="16"><path d="M2 1l11 7-11 7z" fill="#222"/></svg></span></div><p>Phasellus varius nisl et diam eleifend, et interdum</p></div>
    <div class="program"><div class="program-thumb" role="img" aria-label="Comedian holding a microphone in a bright room" style="background:linear-gradient(135deg,#e8e8e8,#b9c2c6 55%,#7f8f96)"><span class="play"><svg width="14" height="16"><path d="M2 1l11 7-11 7z" fill="#222"/></svg></span></div><p>Phasellus varius nisl et diam eleifend, et interdum</p></div>
  </div>
</section>

<section class="contact">
  <h2 class="title">Contact Us</h2>
  <div class="field" style="left:133px;top:114px;width:216px">Name</div>
  <div class="field" style="left:372px;top:114px;width:216px">Email</div>
  <div class="field" style="left:611px;top:114px;width:216px">Phone</div>
  <div class="field" style="left:851px;top:114px;width:216px">City</div>
  <div class="field" style="left:133px;top:172px;width:934px">Message</div>
  <span class="btn-submit">SUBMIT</span>
</section>

<footer class="site-footer">
  <div class="footer-nav">Home<span>|</span>About<span>|</span>Venues<span>|</span>Comics<span>|</span>Performers<span>|</span>Contact</div>
  <div class="copyright">Copyright © 2017 &nbsp;Company name. &nbsp;All rights reserved.</div>
  <div class="social" aria-label="Social media links"><span aria-label="Social link 1"></span><span aria-label="Social link 2"></span><span aria-label="Social link 3"></span></div>
</footer>

</body>
</html>
```